Buch-/eBook-Cover für Traumatherapeutin
Zielgruppe
Ich bin Traumatherapeutin und schreibe ein Buch zum Thema Trauma bearbeiten.
Meine Zielgruppe sucht Heilung, Genesung, Selbstliebe etc.
Aufgabenstellung
Buchcover
Bitte erstell mir ein modernes positives inspirierendes Buchcover mit dem
Titel: 'Morgenlicht NEU entdecken“
Untertitel: „Spüre den Mut der ganz in dir wohnt“
Dr. Mira Kessow
Ich hätte gerne ein modernes Buch, das entweder einen Bezug zum Thema Trauma hat oder aber einfach stylische Schriftzüge. Bin aber auch offen für andere Vorschläge.
Dunkelblau, weiß und türkis oder auch rosa mag ich ganz gerne. Wobei Dunkelblau, weiß und türkis meine Favoriten sind und mit rosa höchstens kleinere Akzente gesetzt werden sollten.
Das Buchcover soll modern sein und direkt ansprechen. Gerne eine originelle Lösung, oder etwas Besonderes, etwas das Tiefe ausdrückt, oder man mehrmals hinsehen muss um etwas zu erkennen oder etwas das mehr Interpretationsspielraum lässt.
Gerne auch viel weiß, zumindest heller und nicht zu dunkel. Stylish, aber nicht überfrachtet.
Schreib mich gerne an, wenn du Fragen hast.
Ich habe mal zwei Beispiel von Typolösungen angehängt, die ich ganz cool fände.
Ich freue mich auf deine Ideen :-)
Ganz liebe Grüße
Mira

```html
<!DOCTYPE html>
<html lang="de">
<head>
<meta charset="utf-8">
<title>Morgenlicht NEU entdecken – Dr. Mira Kessow</title>
<link rel="stylesheet" href="https://fonts.googleapis.com/css2?family=Bebas+Neue&family=Open+Sans:ital,wght@0,400;1,400&family=Sacramento&display=swap">
<style>
  :root {
    --bg-top: #d6a6c6;
    --bg-mid: #bcc3cc;
    --bg-bottom: #a8dbd3;
    --purple: #5b3a96;
    --white: #ffffff;
    --pink-accent: #e38fc2;
    --teal-accent: #7cc6ba;
  }
  html, body {
    margin: 0;
    padding: 0;
    overflow: hidden;
    background: #f2f2f2;
  }
  .cover {
    position: relative;
    width: 858px;
    height: 1200px;
    overflow: hidden;
    background: linear-gradient(170deg, var(--bg-top) 0%, var(--bg-mid) 35%, var(--bg-bottom) 65%, var(--bg-bottom) 100%);
    font-family: "Open Sans", Arial, sans-serif;
  }
  .cover__pattern {
    position: absolute;
    inset: 0;
    width: 858px;
    height: 1200px;
  }
  .cover__author {
    position: absolute;
    top: 48px;
    left: 0;
    width: 858px;
    text-align: center;
    color: var(--white);
    font-size: 27px;
    letter-spacing: 0.5px;
    margin: 0;
  }
  .title {
    margin: 0;
    font-weight: normal;
  }
  .title__script {
    position: absolute;
    font-family: "Sacramento", cursive;
    color: var(--purple);
    line-height: 1;
    white-space: nowrap;
  }
  .title__script--top {
    top: 300px;
    left: 50px;
    font-size: 170px;
  }
  .title__script--bottom {
    top: 600px;
    right: 40px;
    font-size: 130px;
  }
  .title__main {
    position: absolute;
    top: 440px;
    left: 0;
    width: 858px;
    text-align: center;
    font-family: "Bebas Neue", Impact, sans-serif;
    font-size: 240px;
    line-height: 1;
    letter-spacing: 4px;
    color: var(--white);
    text-shadow: -12px -12px 0 var(--purple);
  }
  .cover__subtitle {
    position: absolute;
    top: 760px;
    right: 112px;
    margin: 0;
    text-align: right;
    color: var(--purple);
    font-style: italic;
    font-size: 27px;
    line-height: 1.45;
  }
  .cover__badge {
    position: absolute;
    left: 0;
    top: 0;
    width: 858px;
    height: 1200px;
  }
</style>
</head>
<body>
  <main class="cover">
    <svg class="cover__pattern" viewBox="0 0 858 1200" aria-hidden="false">
      <defs>
        <linearGradient id="pattern-pink" x1="0" y1="0" x2="1" y2="1">
          <stop offset="0" stop-color="#e38fc2" stop-opacity="0.35"/>
          <stop offset="1" stop-color="#e38fc2" stop-opacity="0.15"/>
        </linearGradient>
        <linearGradient id="pattern-teal" x1="0" y1="0" x2="1" y2="1">
          <stop offset="0" stop-color="#7cc6ba" stop-opacity="0.4"/>
          <stop offset="1" stop-color="#7cc6ba" stop-opacity="0.2"/>
        </linearGradient>
      </defs>
      <polygon role="img" aria-label="Dekoratives Linienmuster in Rosa" points="320,0 858,0 858,470" fill="url(#pattern-pink)"/>
      <polygon role="img" aria-label="Dekoratives Linienmuster in Türkis" points="0,735 858,1160 858,1200 0,1200" fill="url(#pattern-teal)"/>
    </svg>

    <p class="cover__author">Dr. Mira Kessow</p>

    <h1 class="title">
      <span class="title__script title__script--top">Morgenlicht</span>
      <span class="title__main">NEU</span>
      <span class="title__script title__script--bottom">entdecken</span>
    </h1>

    <p class="cover__subtitle">Spüre den Mut<br>der ganz in dir wohnt</p>

    <svg class="cover__badge" viewBox="0 0 858 1200" role="img" aria-label="Auszeichnungsbanner">
      <polygon points="605,963 858,963 858,1087 540,1087" fill="#5b3a96"/>
    </svg>
  </main>
</body>
</html>
```